Jolly Hounds Dog Behaviour, Training and Natural Healthcare Business Card Design

I am an experienced and qualified dog behavioural trainer and natural animal healthcare consultant offering a range of services to help pet dog owners with the "whole dog".
COLOURS: A soft light blue in the background - can be fading out or split, red should also feature
LOGO: Dog, healing hands, silhouette, shadow
SERVICES: Behaviour Consults, Training, Complex Skills Coaching Walking Coaching, Diet & Nutrition, Environmental Enrichment, Lifestyle and Lifestage Adaptations, Massage, Natural Health Options
BY LINE: Happy Dogs, Happy Owners
VALUES: Promoting communication and connection between dogs and their owners.
FOCUS: Nutritional guidance and environmental adaptation are often needed to complete the package and increase the success rate of training and behaviour modification.

Target Market(s)

Everyone who has a dog who they wish to improve their relationship with

Industry/Entity Type

Communication

Contact Information for Business Card

Jolly Hounds, Rebecca Thornbury, 0427 861350, jollyhounds7@fernpost.example, www.jollyhounds7.example, Qualified Dog Behavioural Trainer and Natural Animal Healthcare Consultant

Font styles to use
Sans Serif
Script

Colors
85cae6
ec2027

Requirements
Must have
• A clear indication that it is a dog services business. A raised feature
Should not have
• Pawprints, cartoons

```html
<!DOCTYPE html>
<html lang="en">
<head>
<meta charset="utf-8">
<title>Jolly Hounds – Business Card Design</title>
<link rel="stylesheet" href="https://fonts.googleapis.com/css2?family=Cinzel:wght@400;700;900&family=Marcellus&display=swap">
<style>
  :root {
    --page: #ffffff;
    --sky-top: #4fa6d6;
    --sky-mid: #85cae6;
    --band: #ffffff;
    --sea: #3a7fc4;
    --sea-deep: #2f64ad;
    --brand-red: #ec2027;
    --ink: #0d1f3c;
    --silver: #eef2f6;
    --contact: #f4f8fc;
    --tagline: #f7941d;
    --dog-light: #f3ece2;
    --dog-tan: #c8955a;
  }
  * { box-sizing: border-box; margin: 0; padding: 0; }
  html, body { width: 1200px; height: 327px; overflow: hidden; background: var(--page); }
  .canvas { position: relative; width: 1200px; height: 327px; }

  .card {
    position: absolute; top: 22px; width: 448px; height: 256px;
    overflow: hidden; box-shadow: 3px 4px 6px rgba(0,0,0,0.35);
  }
  .card--wide-title { left: 83px; }
  .card--stacked-title { left: 595px; }
  .card__background { position: absolute; inset: 0; width: 100%; height: 100%; }

  .card__name {
    position: absolute; text-align: center; white-space: nowrap;
    font-family: "Cinzel", serif; font-weight: 900; color: var(--brand-red);
    letter-spacing: 1px; line-height: 1;
  }
  .card__owner {
    position: absolute; text-align: center; white-space: nowrap;
    font-family: "Cinzel", serif; font-weight: 400; color: var(--silver);
    text-shadow: 1px 1px 1px #333; letter-spacing: 1px; line-height: 1;
  }
  .card__role {
    position: absolute; text-align: center;
    font-family: "Cinzel", serif; font-weight: 700; color: var(--ink);
    line-height: 1.3; white-space: nowrap;
  }
  .card__services {
    position: absolute; font-family: "Cinzel", serif; font-weight: 400;
    color: var(--ink); white-space: nowrap;
  }
  .card__contact {
    position: absolute; font-family: "Marcellus", serif; color: var(--contact);
    list-style: none; white-space: nowrap; text-shadow: 0 1px 1px rgba(0,0,0,0.35);
  }
  .card__contact .phone { font-size: 15px; }
  .card__contact .phone-label { margin-right: 14px; }
  .card__tagline {
    position: absolute; font-family: "Cinzel", serif; font-weight: 700;
    color: var(--tagline); line-height: 1.2; white-space: nowrap;
    text-shadow: 1px 1px 1px #333;
  }
  .card__dog-photo {
    position: absolute;
    background: radial-gradient(ellipse at 45% 40%, var(--dog-light) 0%, #e6d7c3 45%, var(--dog-tan) 85%, rgba(200,149,90,0) 100%);
  }

  /* first variant */
  .card--wide-title .card__name { top: 14px; left: 0; width: 448px; font-size: 32px; }
  .card--wide-title .card__owner { top: 54px; left: 0; width: 448px; font-size: 16px; }
  .card--wide-title .card__role { top: 78px; left: 0; width: 448px; font-size: 11px; }
  .card--wide-title .card__services { top: 114px; left: 26px; font-size: 10.5px; line-height: 15px; }
  .card--wide-title .card__contact { top: 166px; left: 26px; font-size: 13px; line-height: 20px; }
  .card--wide-title .card__tagline { top: 178px; left: 209px; font-size: 11px; }
  .card--wide-title .card__dog-photo { left: 312px; top: 118px; width: 136px; height: 138px; border-radius: 48% 40% 0 0; }

  /* second variant */
  .card--stacked-title .card__name { top: 20px; left: 0; width: 334px; font-size: 34px; }
  .card--stacked-title .card__owner { top: 64px; left: 0; width: 330px; font-size: 16px; }
  .card--stacked-title .card__role { top: 88px; left: 0; width: 330px; font-size: 10.5px; }
  .card--stacked-title .card__services { top: 140px; left: 0; width: 310px; text-align: center; font-size: 10.5px; line-height: 14px; }
  .card--stacked-title .card__contact { top: 188px; left: 26px; font-size: 13px; line-height: 18px; }
  .card--stacked-title .card__tagline { top: 205px; left: 212px; font-size: 10.5px; }
  .card--stacked-title .card__dog-photo { left: 308px; top: 10px; width: 140px; height: 246px; border-radius: 50% 30% 0 30%; }
</style>
</head>
<body>
<main class="canvas">

  <article class="card card--wide-title">
    <svg class="card__background" viewBox="0 0 448 256" preserveAspectRatio="none" aria-hidden="true">
      <defs>
        <linearGradient id="skyWide" x1="0" y1="0" x2="0" y2="1">
          <stop offset="0" stop-color="var(--sky-top)"/>
          <stop offset="1" stop-color="var(--sky-mid)"/>
        </linearGradient>
        <linearGradient id="bandWide" x1="0" y1="0" x2="0" y2="1">
          <stop offset="0" stop-color="#cfeaf6"/>
          <stop offset="0.5" stop-color="var(--band)"/>
          <stop offset="1" stop-color="#d6eef8"/>
        </linearGradient>
        <linearGradient id="seaWide" x1="0" y1="0" x2="0" y2="1">
          <stop offset="0" stop-color="var(--sea)"/>
          <stop offset="1" stop-color="var(--sea-deep)"/>
        </linearGradient>
      </defs>
      <rect width="448" height="256" fill="url(#skyWide)"/>
      <path d="M0 110 Q220 100 448 108 L448 152 Q220 146 0 158 Z" fill="url(#bandWide)"/>
      <path d="M0 158 Q220 146 448 152 L448 256 L0 256 Z" fill="url(#seaWide)"/>
    </svg>
    <h1 class="card__name">Jolly Hounds</h1>
    <p class="card__owner">Rebecca Thornbury</p>
    <p class="card__role">Qualified Dog Behavioural Trainer and Natural Animal<br>Healthcare Consultant</p>
    <p class="card__services">Behaviour Consults, Training, Complex Skills,<br>Walking Coaching, Diet &amp; Nutrition, Adaptations,<br>Massage, Natural Health Options</p>
    <ul class="card__contact">
      <li class="phone"><span class="phone-label">Phone</span>0427 861350</li>
      <li>www.jollyhounds7.example</li>
      <li>jollyhounds7@fernpost.example</li>
    </ul>
    <p class="card__tagline">Happy Dogs,<br>Happy Owners</p>
    <div class="card__dog-photo" role="img" aria-label="Photo of a smiling beagle wearing a dark collar"></div>
  </article>

  <article class="card card--stacked-title">
    <svg class="card__background" viewBox="0 0 448 256" preserveAspectRatio="none" aria-hidden="true">
      <defs>
        <linearGradient id="skyStacked" x1="0" y1="0" x2="0" y2="1">
          <stop offset="0" stop-color="var(--sky-top)"/>
          <stop offset="1" stop-color="var(--sky-mid)"/>
        </linearGradient>
        <linearGradient id="bandStacked" x1="0" y1="0" x2="0" y2="1">
          <stop offset="0" stop-color="#cfeaf6"/>
          <stop offset="0.5" stop-color="var(--band)"/>
          <stop offset="1" stop-color="#d6eef8"/>
        </linearGradient>
        <linearGradient id="seaStacked" x1="0" y1="0" x2="0" y2="1">
          <stop offset="0" stop-color="var(--sea)"/>
          <stop offset="1" stop-color="var(--sea-deep)"/>
        </linearGradient>
      </defs>
      <rect width="448" height="256" fill="url(#skyStacked)"/>
      <path d="M0 134 Q220 126 448 132 L448 180 Q220 176 0 186 Z" fill="url(#bandStacked)"/>
      <path d="M0 186 Q220 176 448 180 L448 256 L0 256 Z" fill="url(#seaStacked)"/>
    </svg>
    <h1 class="card__name">Jolly Hounds</h1>
    <p class="card__owner">Rebecca Thornbury</p>
    <p class="card__role">Qualified Dog Behavioural Trainer<br>and Natural Animal Healthcare<br>Consultant</p>
    <p class="card__services">Behaviour Consults, Training, Complex Skills,<br>Walking Coaching, Diet &amp; Nutrition,<br>Massage, Natural Health Options</p>
    <ul class="card__contact">
      <li class="phone"><span class="phone-label">Phone</span>0427 861350</li>
      <li>www.jollyhounds7.example</li>
      <li>jollyhounds7@fernpost.example</li>
    </ul>
    <p class="card__tagline">Happy Dogs,<br>Happy Owners</p>
    <div class="card__dog-photo" role="img" aria-label="Close-up photo of a smiling beagle with a dark collar"></div>
  </article>

</main>
</body>
</html>
```